KBT Business Cards

We require business cards for our business. We would like a matte black back to the card, with our logo centred in the middle. The front side of the card is open to design.

Target Market(s)

Clients looking for legal services (professional)

Industry/Entity Type

Legal

Contact Information for Business Card

Doran Kelbrath
Partner
Mobile: 0461 738 524
Email: doran@kbtlaw.co
Website: www.kbtlaw.co
Level 3, 118 Wendmore Street
Sydney NSW 2000

Font styles to use
Other font styles liked:
• Avenir

Colors
f04a50
ffffff
1b1b1b

Requirements
Must have
• Black back with logo included in the centre of the card.
• Our font is Avenir.

```html
<!DOCTYPE html>
<html lang="en">
<head>
<meta charset="utf-8">
<title>KBT Business Cards</title>
<link href="https://fonts.googleapis.com/css2?family=Nunito+Sans:wght@400;600;700&display=swap" rel="stylesheet">
<style>
  :root {
    --brand-red: #f04a50;
    --brand-white: #ffffff;
    --brand-black: #1b1b1b;
    --card-black: #1e1e1e;
    --stage: #e9e7e5;
    --muted: #e6e6e6;
  }
  * { box-sizing: border-box; margin: 0; padding: 0; }
  html, body {
    width: 1200px; height: 715px; overflow: hidden;
    background: var(--stage);
    font-family: "Nunito Sans", "Avenir", sans-serif;
  }
  .canvas {
    position: relative; width: 1200px; height: 715px;
    display: flex; align-items: center; justify-content: center; gap: 60px;
  }
  .card {
    position: relative; width: 520px; height: 297px;
    border-radius: 3px; overflow: hidden;
    box-shadow: 0 10px 26px rgba(0,0,0,.22);
  }
  .card-back { background: var(--card-black); border-bottom: 4px solid var(--brand-red); }
  .card-front { background: var(--card-black); }

  .wordmark {
    display: flex; align-items: center; gap: 16px;
    font-weight: 700; text-transform: uppercase;
    line-height: 1.02; letter-spacing: .5px;
  }
  .wordmark-square { width: 44px; height: 44px; background: var(--brand-red); flex: none; }
  .wordmark-name { font-size: 22px; }
  .card-back .wordmark {
    position: absolute; left: 50%; top: 50%; transform: translate(-50%, -50%);
    color: var(--brand-white);
  }

  .front-shape { position: absolute; inset: 0; }
  .card-front .wordmark {
    position: absolute; left: 350px; top: 160px; transform: translate(-50%, -50%);
    color: var(--brand-black);
  }
  .card-front .wordmark-name { font-size: 19px; }
  .card-front .wordmark-square { width: 36px; height: 36px; }

  .contact { position: absolute; left: 34px; top: 46px; color: var(--muted); }
  .contact-name {
    color: var(--brand-red); font-weight: 600; font-size: 18px;
    text-transform: uppercase; letter-spacing: .5px;
  }
  .contact-title { font-size: 12.5px; margin-top: 1px; }
  .contact-address { font-size: 12.5px; margin-top: 14px; line-height: 1.35; }
  .contact-list { list-style: none; margin-top: 10px; font-size: 12.5px; line-height: 1.5; }
  .contact-list li { display: flex; align-items: center; gap: 8px; }
  .contact-list svg { width: 9px; height: 9px; flex: none; }
</style>
</head>
<body>
<main class="canvas">

  <section class="card card-back" aria-label="Card back">
    <div class="wordmark">
      <span class="wordmark-square"></span>
      <span class="wordmark-name">Kelbrath<br>Brandt<br>Tolley</span>
    </div>
  </section>

  <section class="card card-front" aria-label="Card front">
    <svg class="front-shape" viewBox="0 0 520 297" aria-hidden="true">
      <circle cx="400" cy="168" r="170" fill="none" stroke="var(--brand-red)" stroke-width="3"/>
      <circle cx="410" cy="172" r="165" fill="var(--brand-white)"/>
    </svg>

    <div class="contact">
      <p class="contact-name">Doran Kelbrath</p>
      <p class="contact-title">General Manager</p>
      <p class="contact-address">118 Wendmore St<br>Sydney NSW 2000</p>
      <ul class="contact-list">
        <li>
          <svg viewBox="0 0 10 10"><path d="M2 0.5 L4 2.6 L3 3.8 Q4.2 6 6.2 7 L7.4 6 L9.5 8 L8.2 9.5 Q3 9 0.5 1.8 Z" fill="var(--brand-red)"/></svg>
          0461 738 524
        </li>
        <li>
          <svg viewBox="0 0 10 10"><rect x="0.7" y="2" width="8.6" height="6" fill="none" stroke="var(--brand-red)" stroke-width="1.2"/><path d="M0.7 2 L5 5.5 L9.3 2" fill="none" stroke="var(--brand-red)" stroke-width="1.2"/></svg>
          doran@kbtlaw.co
        </li>
        <li>
          <svg viewBox="0 0 10 10"><circle cx="5" cy="5" r="4.2" fill="none" stroke="var(--brand-red)" stroke-width="1.2"/><path d="M0.8 5 H9.2 M5 0.8 Q2.5 5 5 9.2 M5 0.8 Q7.5 5 5 9.2" fill="none" stroke="var(--brand-red)" stroke-width="0.9"/></svg>
          www.kbtlaw.co
        </li>
      </ul>
    </div>

    <div class="wordmark">
      <span class="wordmark-square"></span>
      <span class="wordmark-name">Kelbrath<br>Brandt<br>Tolley</span>
    </div>
  </section>

</main>
</body>
</html>
```